Harbourline Physiotherapy business card design

We need a fresh, new business card design for our physiotherapy clinic Harbourline Physiotherapy

Will attach logo soon we had logo designed from our last project

Industry/Entity Type

Physical Therapy

Contact Information for Business Card

On front
Needs our logo, contact details:
58 Wexley Lane Marlow Vale NSW 2804
Ph/f: 02 9481 2057
info@harbourlinephysio.example.com.au

Requirements
Must have
• On the back of the card needs to have area to write down follow up appointments
• On front
• Needs our logo
• The colours have to be the colours in our logo which are: sky blue, black and white
• Font to be same as our logo please
• We want the card to look simple, not too cluttered but to the point
Should not have
• We don't need any extra pictures other than our logo

```html
<!DOCTYPE html>
<html lang="en">
<head>
<meta charset="utf-8">
<title>Harbourline Physiotherapy business card</title>
<link rel="stylesheet" href="https://fonts.googleapis.com/css2?family=Open+Sans:wght@400;600;700&display=swap">
<style>
  :root {
    --sky: #2f7fd0;
    --ink: #1d1d1f;
    --grey: #3a3a3c;
    --paper: #ffffff;
    --backdrop: #e4e6ea;
  }
  * { box-sizing: border-box; margin: 0; padding: 0; }
  html, body {
    width: 1200px; height: 900px; overflow: hidden;
    background: var(--backdrop);
    font-family: "Open Sans", sans-serif;
  }
  .canvas { position: relative; width: 1200px; height: 900px; }
  .card {
    position: absolute; width: 620px; height: 354px;
    background: var(--paper); border-radius: 22px; overflow: hidden;
    box-shadow: 0 10px 28px rgba(0,0,0,.18);
  }
  .card--back { left: 60px; top: 70px; }
  .card--front { left: 520px; top: 476px; }
  .card__wave { position: absolute; inset: 0; width: 100%; height: 100%; }

  .brand {
    position: absolute; display: flex; align-items: center; gap: 12px;
    color: var(--sky); font-weight: 600; line-height: 1.05;
  }
  .brand__dot { width: 34px; height: 34px; border-radius: 50%; background: var(--sky); flex: none; }
  .brand__name { font-size: 30px; }
  .brand__name span { display: block; }
  .card--back .brand { left: 330px; top: 46px; }
  .card--front .brand { left: 40px; top: 148px; }

  .appointments { position: absolute; left: 40px; top: 168px; color: var(--sky); font-size: 15px; }
  .appointments__title { margin-bottom: 10px; }
  .appointments__row { display: flex; align-items: flex-end; gap: 6px; height: 30px; padding-left: 18px; }
  .appointments__line { width: 260px; border-bottom: 1px dashed var(--sky); margin-bottom: 5px; }

  .contact {
    position: absolute; left: 318px; top: 92px; padding-left: 16px;
    border-left: 1.5px solid var(--grey); color: var(--grey); font-size: 13.5px; line-height: 1.45;
  }
  .contact__name { font-size: 26px; font-weight: 700; color: var(--ink); letter-spacing: .5px; margin-bottom: 6px; }
  .contact__name span { color: var(--sky); }
  .contact__item { display: flex; align-items: center; gap: 8px; }
  .contact__item svg { width: 12px; height: 12px; fill: var(--sky); flex: none; }
  .contact__address { margin-bottom: 6px; }
</style>
</head>
<body>
<main class="canvas">

  <section class="card card--back" aria-label="Card back">
    <svg class="card__wave" viewBox="0 0 620 354" preserveAspectRatio="none" aria-hidden="true">
      <path d="M0 354 L0 346 C300 342 500 305 620 205 L620 354 Z" fill="var(--sky)"/>
      <path d="M0 344 C300 340 500 303 620 203" fill="none" stroke="#fff" stroke-width="4"/>
      <path d="M170 336 C360 328 520 285 620 188" fill="none" stroke="var(--ink)" stroke-width="3"/>
    </svg>
    <div class="brand">
      <div class="brand__dot"></div>
      <div class="brand__name"><span>Harbourline</span><span>Physiotherapy</span></div>
    </div>
    <div class="appointments">
      <p class="appointments__title">Appointments:</p>
      <div class="appointments__row">Name: <span class="appointments__line"></span></div>
      <div class="appointments__row">Time: <span class="appointments__line"></span></div>
      <div class="appointments__row">Date: <span class="appointments__line"></span></div>
    </div>
  </section>

  <section class="card card--front" aria-label="Card front">
    <svg class="card__wave" viewBox="0 0 620 354" preserveAspectRatio="none" aria-hidden="true">
      <path d="M0 354 L0 332 C200 352 420 300 620 238 L620 354 Z" fill="var(--sky)"/>
      <path d="M0 330 C200 350 420 298 620 236" fill="none" stroke="#fff" stroke-width="4"/>
      <path d="M0 346 C200 358 420 318 620 256" fill="none" stroke="var(--ink)" stroke-width="2.5"/>
    </svg>
    <div class="brand">
      <div class="brand__dot"></div>
      <div class="brand__name"><span>Harbourline</span><span>Physiotherapy</span></div>
    </div>
    <div class="contact">
      <p class="contact__name">MARA <span>ELLISON</span></p>
      <p class="contact__address">58 Wexley Lane<br>Marlow Vale NSW 2804</p>
      <p class="contact__item">
        <svg viewBox="0 0 24 24" aria-hidden="true"><path d="M6.6 10.8a15 15 0 0 0 6.6 6.6l2.2-2.2a1 1 0 0 1 1-.25 11.4 11.4 0 0 0 3.6.57 1 1 0 0 1 1 1V20a1 1 0 0 1-1 1A17 17 0 0 1 3 4a1 1 0 0 1 1-1h3.5a1 1 0 0 1 1 1c0 1.25.2 2.45.57 3.6a1 1 0 0 1-.25 1z"/></svg>
        02 9481 2057
      </p>
      <p class="contact__item">
        <svg viewBox="0 0 24 24" aria-hidden="true"><path d="M2 5h20v14H2z M4 7v.5l8 5 8-5V7l-8 5z" fill-rule="evenodd"/></svg>
        info@harbourlinephysio.example.com.au
      </p>
    </div>
  </section>

</main>
</body>
</html>
```